Executive Business Card for Healthcare Company [Need Today]

I need a business card design for a healthcare company. The only branding the company has thus far is a logo. The cards will be utilized by company executives. The design I envision will be vibrant and appealing but with a corporate feel. They shouldn't be too casual or playful. I would like to complete this project TODAY if possible.

Target Market(s)

Healthcare vendors, other executives in healthcare and pharmaceuticals

Industry/Entity Type

Pharmaceutical

Contact Information for Business Card

See attachment

Font styles to use
Serif
Sans Serif

Colors

Designer to choose colors to be used in the design.

```html
<!DOCTYPE html>
<html lang="en">
<head>
<meta charset="utf-8">
<title>Tavira Therapeutics – Executive Business Card</title>
<link href="https://fonts.googleapis.com/css2?family=Mulish:wght@300;400;600;700&display=swap" rel="stylesheet">
<style>
  :root {
    --teal: #17b8c0;
    --teal-deep: #13a6ae;
    --green: #4cc08f;
    --charcoal: #38393b;
    --paper: #ffffff;
    --grey-text: #555659;
    --backdrop: #e9e7e3;
  }
  * { box-sizing: border-box; margin: 0; padding: 0; }
  html, body {
    width: 1200px; height: 800px; overflow: hidden;
    background: var(--backdrop);
    font-family: "Mulish", Arial, sans-serif;
  }
  .canvas { position: relative; width: 1200px; height: 800px; }
  .card {
    position: absolute; width: 540px; height: 309px;
    border-radius: 4px; overflow: hidden;
    box-shadow: 0 10px 28px rgba(0,0,0,.16);
  }
  .card svg.card-shapes { position: absolute; inset: 0; }

  /* Front */
  .card-front { left: 45px; top: 130px; background: var(--teal); }
  .front-pattern { position: absolute; left: 0; top: 0; width: 540px; height: 188px; background: linear-gradient(135deg, var(--teal) 0%, var(--teal-deep) 100%); }
  .front-brand { position: absolute; left: 78px; top: 52px; display: flex; align-items: center; gap: 20px; color: var(--paper); }
  .brand-circle { width: 94px; height: 94px; border: 3px solid currentColor; border-radius: 50%; flex: none; }
  .brand-name { font-weight: 300; font-size: 34px; line-height: 1; letter-spacing: .5px; }
  .front-address { position: absolute; right: 40px; top: 212px; text-align: right; color: var(--paper); }
  .front-address .company { font-weight: 700; font-size: 18px; }
  .front-address .street { font-weight: 400; font-size: 17px; margin-top: 6px; }

  /* Back */
  .card-back { left: 615px; top: 360px; background: var(--paper); }
  .back-brand { position: absolute; left: 34px; top: 36px; display: flex; align-items: center; gap: 16px; color: var(--teal); }
  .back-brand .brand-circle { width: 72px; height: 72px; border-color: var(--green); }
  .back-brand .brand-name { font-size: 27px; }
  .holder { position: absolute; right: 34px; top: 118px; text-align: right; color: var(--charcoal); }
  .holder .name { font-weight: 700; font-size: 24px; }
  .holder .title { font-weight: 400; font-size: 15px; margin-top: 2px; }
  .contacts { position: absolute; left: 0; right: 0; top: 212px; display: flex; justify-content: space-around; padding: 0 16px; }
  .contact { display: flex; flex-direction: column; align-items: center; gap: 8px; color: var(--paper); font-size: 15px; letter-spacing: .3px; }
  .contact-icon { width: 24px; height: 24px; border-radius: 6px; background: var(--green); display: flex; align-items: center; justify-content: center; }
</style>
</head>
<body>
<main class="canvas">

  <section class="card card-front" aria-label="Card front">
    <div class="front-pattern" role="img" aria-label="Faint repeating brand-mark pattern on teal"></div>
    <svg class="card-shapes" width="540" height="309" viewBox="0 0 540 309">
      <rect x="0" y="188" width="540" height="96" fill="var(--charcoal)"/>
      <rect x="0" y="284" width="540" height="25" fill="var(--teal)"/>
    </svg>
    <div class="front-brand">
      <span class="brand-circle"></span>
      <span class="brand-name">Tavira Therapeutics</span>
    </div>
    <div class="front-address">
      <p class="company">Tavira Therapeutics</p>
      <p class="street">118 W Harbor Street, Suite 201</p>
    </div>
  </section>

  <section class="card card-back" aria-label="Card back">
    <svg class="card-shapes" width="540" height="309" viewBox="0 0 540 309">
      <polygon points="0,180 200,180 540,196 540,309 0,309" fill="var(--charcoal)"/>
      <polygon points="200,172 540,188 540,196 200,180" fill="var(--green)"/>
      <polygon points="0,282 272,282 290,309 0,309" fill="var(--teal)"/>
    </svg>
    <div class="back-brand">
      <span class="brand-circle"></span>
      <span class="brand-name">Tavira Therapeutics</span>
    </div>
    <div class="holder">
      <p class="name">Martin Hale</p>
      <p class="title">Senior Director of Marketing</p>
    </div>
    <div class="contacts">
      <div class="contact">
        <span class="contact-icon">
          <svg width="14" height="14" viewBox="0 0 24 24"><path fill="#fff" d="M6.6 10.8a15.1 15.1 0 0 0 6.6 6.6l2.2-2.2a1 1 0 0 1 1-.25 11.4 11.4 0 0 0 3.6.57 1 1 0 0 1 1 1V20a1 1 0 0 1-1 1A17 17 0 0 1 3 4a1 1 0 0 1 1-1h3.5a1 1 0 0 1 1 1c0 1.25.2 2.45.57 3.57a1 1 0 0 1-.25 1z"/></svg>
        </span>
        <span>555-201-4830</span>
      </div>
      <div class="contact">
        <span class="contact-icon">
          <svg width="14" height="14" viewBox="0 0 24 24"><rect x="3" y="6" width="18" height="12" rx="1" fill="none" stroke="#fff" stroke-width="2"/><path d="M3 7l9 6 9-6" fill="none" stroke="#fff" stroke-width="2"/></svg>
        </span>
        <span>mhale@tavirarx.com</span>
      </div>
      <div class="contact">
        <span class="contact-icon">
          <svg width="14" height="14" viewBox="0 0 24 24"><rect x="7" y="2" width="10" height="20" rx="2" fill="none" stroke="#fff" stroke-width="2"/><circle cx="12" cy="18" r="1.2" fill="#fff"/></svg>
        </span>
        <span>555-302-7715</span>
      </div>
    </div>
  </section>

</main>
</body>
</html>
```